Hip surgeon needs a educative book cover design

I need to re-design my old book cover for its 3rd edition.
It's a small book dedicated to my patients, who underwent total hip replacement. It's meant to help people getting around the basic care after a total hip replacement surgery and getting back to their normal, active life.
The title is: "Morning light rituals: a quiet companion".
I already had a new logo, new stationery and new website design from ArtFolio (please see the attachments).
The final design should be look alike the other fresh new designs. It must communicate health, peacefulness.
I also attached the manual as it looks today for reference.
A5 size.
Just cover and back cover.
Health

```html
<!DOCTYPE html>
<html lang="en">
<head>
<meta charset="utf-8">
<title>Morning light rituals: a quiet companion — cover</title>
<link rel="stylesheet" href="https://fonts.googleapis.com/css2?family=Roboto+Condensed:wght@300;400&display=swap">
<style>
  :root {
    --sky: #a8c7e7;
    --column-blue: #5b93cd;
    --band-blue: #2b80c2;
    --ink: #111418;
    --paper: #ffffff;
    --scan-dark: #0b1418;
    --scan-teal: #2f8f9a;
    --scan-gold: #c9b73a;
  }
  * { margin: 0; padding: 0; box-sizing: border-box; }
  html, body { width: 890px; height: 1200px; overflow: hidden; background: var(--paper); }
  .cover {
    position: relative;
    width: 890px;
    height: 1200px;
    background: var(--paper);
    font-family: "Roboto Condensed", "Arial Narrow", sans-serif;
    overflow: hidden;
  }
  .sky-panel {
    position: absolute; left: 0; top: 0;
    width: 890px; height: 540px;
    background: var(--sky);
  }
  .side-column {
    position: absolute; left: 0; top: 0;
    width: 258px; height: 540px;
    background: var(--column-blue);
  }
  .title {
    position: absolute; left: 62px; top: 330px;
    color: var(--ink);
    line-height: 1.1;
  }
  .title-main { display: block; font-weight: 400; font-size: 68px; letter-spacing: -0.5px; }
  .title-sub { display: block; font-weight: 300; font-size: 60px; }
  .scan-image {
    position: absolute; left: 258px; top: 540px;
    width: 632px; height: 430px;
    background:
      radial-gradient(ellipse at 50% 20%, rgba(120,200,210,0.55), transparent 45%),
      radial-gradient(ellipse at 25% 80%, rgba(201,183,58,0.8), transparent 40%),
      radial-gradient(ellipse at 78% 80%, rgba(201,183,58,0.75), transparent 40%),
      linear-gradient(180deg, var(--scan-teal) 0%, var(--scan-dark) 55%, #1a1d10 100%);
  }
  .author-band {
    position: absolute; left: 0; top: 970px;
    width: 890px; height: 230px;
    background: var(--band-blue);
    color: var(--paper);
  }
  .author-name {
    position: absolute; left: 62px; top: 72px;
    font-size: 46px; font-weight: 400;
  }
  .author-role {
    position: absolute; left: 62px; top: 130px;
    font-size: 32px; font-weight: 300;
  }
  .brand {
    position: absolute; right: 40px; top: 110px;
    display: flex; align-items: center; gap: 10px;
    font-size: 26px; font-weight: 400; color: var(--paper);
  }
  .brand-dot {
    width: 30px; height: 30px; border-radius: 50%;
    background: var(--paper);
  }
</style>
</head>
<body>
  <main class="cover">
    <div class="sky-panel"></div>
    <div class="side-column"></div>
    <h1 class="title">
      <span class="title-main">Morning light rituals:</span>
      <span class="title-sub">a quiet companion</span>
    </h1>
    <div class="scan-image" role="img" aria-label="Tinted pelvis X-ray image in teal and yellow tones"></div>
    <footer class="author-band">
      <p class="author-name">Dr. Helena R. Vasquez</p>
      <p class="author-role">Cirurgia do Quadril</p>
      <div class="brand"><span class="brand-dot"></span><span>Vasquez</span></div>
    </footer>
  </main>
</body>
</html>
```